Preliminary design concepts for VELURAN history document

To produce three design concepts as a demonstration for the layout of a document with a look and feel compatible with the existing documents/visual identity of an Australia-based NGO. The design concepts will be used to provide concepts to the NGO and ideally select a designer for the longer 30 - 50 page document.

Target Market(s)

Australian heritage community, international heritage community, general population interested in heritage issues and key stakeholders in heritage projects

Colors
0455a3
3176b5
85acd3
ffc214
fece3e
fee18a
f78f20
f37122

Requirements
Must have
• Eye catching but authoritative design to reflect a serious professional organisation, but one which reflects a modern, progressive approach.
• The designer needs to have experience working with document layout in InDesign and/or Illustrator and provide files in a range of outputs including EPS formats as well as HTML and PDF.
Nice to have
• Interplay between images and design elements

```html
<!DOCTYPE html>
<html lang="en">
<head>
<meta charset="utf-8">
<title>The Australia VELURAN inc — Tarrin Charter spread</title>
<link href="https://fonts.googleapis.com/css2?family=EB+Garamond:ital,wght@0,400;0,500;0,600;1,500;1,600&display=swap" rel="stylesheet">
<style>
  :root {
    --paper: #ffffff;
    --ink: #111111;
    --fold: #e2e2e2;
    --caption-blue: #0455a3;
    --tint-light: #a9b3d6;
    --tint-mid: #5f6ca3;
    --tint-dark: #2f3668;
    --mono-light: #e9e9e9;
    --mono-mid: #8a8a8a;
    --mono-dark: #2b2b2b;
  }
  * { margin: 0; padding: 0; box-sizing: border-box; }
  html, body { width: 1200px; height: 848px; overflow: hidden; background: var(--paper); }
  body { font-family: "EB Garamond", Garamond, serif; color: var(--ink); font-weight: 500; }

  .spread { position: relative; width: 1200px; height: 848px; }
  .page { position: absolute; top: 0; height: 848px; }
  .page--left { left: 0; width: 596px; }
  .page--right { left: 596px; width: 604px; border-left: 1px solid var(--fold); }

  .photo { position: absolute; }
  .photo--hero-left {
    left: 58px; top: 62px; width: 481px; height: 335px;
    background: linear-gradient(180deg, var(--tint-light) 0%, #c6cde6 25%, var(--tint-mid) 45%, var(--tint-dark) 65%, var(--tint-mid) 100%);
  }
  .photo__label {
    position: absolute; left: 12px; top: 10px;
    font-size: 7px; color: var(--caption-blue);
  }
  .photo--members {
    left: 57px; top: 432px; width: 109px; height: 82px;
    background: linear-gradient(180deg, #c5cbdd 0%, #8d96b3 60%, #6c7596 100%);
  }
  .photo--hero-right {
    left: 0; top: 0; width: 594px; height: 622px;
    background: linear-gradient(180deg, var(--mono-light) 0%, #d6d6d6 30%, var(--mono-mid) 55%, var(--mono-dark) 100%);
  }

  .caption {
    position: absolute; left: 40px; top: 519px; width: 126px;
    font-size: 7px; line-height: 11px; text-align: right;
  }
  .caption em { font-weight: 600; font-style: italic; }

  .column { position: absolute; font-size: 8.2px; line-height: 16.3px; letter-spacing: -0.05px; }
  .column--one { left: 181px; top: 428px; width: 176px; }
  .column--two { left: 370px; top: 428px; width: 169px; }
  .column--wide { left: 55px; top: 652px; width: 359px; line-height: 16.8px; }

  .line {
    display: block; white-space: nowrap;
    text-align: justify; text-align-last: justify;
  }
  .line--end { text-align-last: left; }

  .folio { position: absolute; top: 767px; font-size: 8px; font-weight: 600; }
  .folio--left { left: 57px; }
  .folio--right { right: 57px; }
  .folio em { font-style: italic; }
</style>
</head>
<body>
<div class="spread">
  <section class="page page--left">
    <div class="photo photo--hero-left" role="img" aria-label="Photograph of a large red monolith rising above desert scrubland, tinted blue">
      <span class="photo__label">Australia VELURAN Members</span>
    </div>
    <div class="photo photo--members" role="img" aria-label="Archival photograph of three members standing in arched openings of an old hospital"></div>
    <p class="caption">Australia VELURAN Members<br>at the Old Kelden Hospital,<br><em>Victoria, 1978.</em></p>

    <div class="column column--one">
      <span class="line">nationally. Australia VELURAN has long been</span>
      <span class="line">active within governance of VELURAN Inter-</span>
      <span class="line">national, contributing its first representative</span>
      <span class="line">to the international Executive Committee of</span>
      <span class="line">VELURAN in 1981 and keeping a representative</span>
      <span class="line line--end">there continually since 1991.</span>
      <span class="line">Numerous Australia VELURAN members are</span>
      <span class="line">participants in the 28 VELURAN Internation-</span>
      <span class="line">al Scientific Committees which meet regularly</span>
      <span class="line">around the globe to develop expertise on specific</span>
      <span class="line">heritage issues and several of these committees</span>
      <span class="line">are chaired by Australia VELURAN members.</span>
      <span class="line">nationally. Australia VELURAN has long been</span>
      <span class="line">active within governance of VELURAN Inter-</span>
      <span class="line">national, contributing its first representative</span>
      <span class="line">to the international Executive Committee of</span>
      <span class="line">VELURAN in 1981 and keeping a representative</span>
      <span class="line line--end">there continually since 1991.</span>
      <span class="line">Numerous Australia VELURAN members are</span>
      <span class="line">participants in the 28 VELURAN Internation-</span>
    </div>

    <div class="column column--two">
      <span class="line">al Scientific Committees which meet regularly</span>
      <span class="line">around the globe to develop expertise on specific</span>
      <span class="line">heritage issues and several of these committees</span>
      <span class="line">are chaired by Australia VELURAN members.</span>
      <span class="line">nationally. Australia VELURAN has long been</span>
      <span class="line">active within governance of VELURAN Inter-</span>
      <span class="line">national, contributing its first representative</span>
      <span class="line">to the international Executive Committee of</span>
      <span class="line">VELURAN in 1981 and keeping a representative</span>
      <span class="line line--end">there continually since 1991.</span>
      <span class="line">Numerous Australia VELURAN members are</span>
      <span class="line">participants in the 28 VELURAN Internation-</span>
      <span class="line">al Scientific Committees which meet regularly</span>
      <span class="line">around the globe to develop expertise on specific</span>
      <span class="line">heritage issues and several of these committees</span>
      <span class="line line--end">are chaired by Australia VELURAN members.</span>
    </div>

    <p class="folio folio--left"><em>12</em> &nbsp;|&nbsp; The Australia VELURAN inc</p>
  </section>

  <section class="page page--right">
    <div class="photo photo--hero-right" role="img" aria-label="Black and white photograph of a ruined stone mine building on a hillside with a low stone wall and scrub"></div>

    <div class="column column--wide">
      <span class="line">the advancement of heritage practice internationally. Australia VELURAN has long been active with-</span>
      <span class="line">in governance of VELURAN International, contributing its first representative to the international</span>
      <span class="line">Executive Committee of VELURAN in 1981 and keeping a representative there continually since</span>
      <span class="line line--end">1991.</span>
      <span class="line">Numerous Australia VELURAN members are participants in the 28 VELURAN International Scientif-</span>
      <span class="line">ic Committees which meet regularly around the globe to develop expertise on specific heritage issues</span>
    </div>

    <p class="folio folio--right">Tarrin Charter &nbsp;|&nbsp; <em>13</em></p>
  </section>
</div>
</body>
</html>
```